Floravine Pte Ltd

I want a creative and stand out web page so when my client search for my web page or google search. The front page is stand out and they know that we are the interior office designer that are searching for . We are commercial office design company. We also have the video to put at our front page for client to see. Natural is the key elements. As we like to carry recycle materials , plant , trees is our key element such as biophilic design
Updates

Hi All,

For my web page, I need minimalist design and creative frontpage.
When my client search for my web page, they straight feel that this is the office design company.
The webpage is special and nature is the key element for the design.
My company logo can be design in the shaped of the letter OO in the webpage.
Below is the sample you can refer.

https://www.pinboardly.example/pin/527190364821057392/

Target Market(s)

Customer searching for office design

Industry/Entity Type

Commerical designer firm- Office interior design & Build company

Number of Pages Required

5+ page

Font styles to use
Other font styles liked:
• Wilmina

Colors
59FF00
82FF00
B8FF75
E3FFCB
F4FFEA
FFC000
F8CF3A
FAE287
FDF2CF
FEFAEE
6B429C
8869AF
B7A5CE
E3DAEB
F3F0F8

Requirements
Must have
• Home, Services,Gallery, Calculator, Testimonials, Contact, Blog
Nice to have
• Natural, creative, minimalist
Should not have
• No black color or blue color

```html
<!DOCTYPE html>
<html lang="en">
<head>
<meta charset="utf-8">
<title>Floravine Pte Ltd – Office Interior Design</title>
<link rel="stylesheet" href="https://fonts.googleapis.com/css2?family=Quicksand:wght@400;500;600;700&family=Open+Sans:wght@400;600;700&display=swap">
<style>
:root{
  --yellow:#FFC000;
  --yellow-soft:#F8CF3A;
  --yellow-pale:#FDF2CF;
  --purple:#6B429C;
  --purple-mid:#8869AF;
  --purple-deep:#4E2C78;
  --purple-pale:#F3F0F8;
  --green-pale:#F4FFEA;
  --ink:#3D3444;
  --ink-soft:#6F6676;
  --white:#FFFFFF;
}
*{margin:0;padding:0;box-sizing:border-box}
html,body{width:1200px;height:4868px;overflow:hidden}
body{position:relative;background:var(--white);font-family:"Open Sans",sans-serif;color:var(--ink)}
.abs{position:absolute}
.section-title{font-family:"Quicksand",sans-serif;font-weight:500;font-size:42px;letter-spacing:1px;color:var(--ink)}

/* header */
.site-header{left:0;top:0;width:1200px;height:112px;background:var(--white);box-shadow:0 2px 8px rgba(61,52,68,.08);z-index:5}
.brand{left:32px;top:26px;display:flex;align-items:center;gap:12px;font-family:"Quicksand",sans-serif;font-weight:700;font-size:30px;color:var(--purple)}
.brand-dot{width:40px;height:40px;border-radius:50%;background:var(--yellow)}
.call-pill{left:760px;top:10px;width:400px;height:38px;border-radius:19px;background:var(--yellow);color:var(--white);font-size:15px;font-weight:700;display:flex;align-items:center;justify-content:center;gap:10px}
.main-nav{left:400px;top:64px;display:flex;gap:34px;font-size:16px;color:var(--ink)}
.main-nav a{color:inherit;text-decoration:none;padding-bottom:8px}
.main-nav a.active{color:var(--yellow);border-bottom:3px solid var(--yellow)}

/* hero */
.hero{left:0;top:112px;width:1200px;height:600px;
  background:
    radial-gradient(ellipse 420px 220px at 830px 300px,#e9e6e0 0%,#c8c4bd 45%,rgba(200,196,189,0) 70%),
    radial-gradient(ellipse 700px 260px at 300px 80px,rgba(255,255,255,.7),rgba(255,255,255,0) 70%),
    linear-gradient(180deg,#a9cbe3 0%,#cfe1ea 38%,#b9cf93 60%,#7fae4e 74%,#4e8a2f 100%)}
.hero-copy{left:92px;top:126px;width:430px;padding:18px 20px;background:rgba(61,52,68,.35);font-family:"Quicksand",sans-serif;font-weight:700;font-size:27px;line-height:35px;color:var(--white);text-transform:uppercase}
.play-btn{left:104px;top:348px;width:56px;height:56px;border-radius:50%;background:var(--yellow)}
.hero-arrow{top:266px;width:44px;height:44px;border-radius:50%;background:rgba(255,255,255,.6)}

/* services */
.services{left:0;top:712px;width:1200px;height:360px;background:var(--white)}
.service{width:240px;text-align:center;font-size:17px;line-height:23px;color:var(--ink)}
.service .photo{width:150px;height:150px;border-radius:50%;margin:0 auto 24px;box-shadow:0 3px 10px rgba(61,52,68,.15)}
.service-card{left:482px;top:-16px;width:236px;height:310px;background:var(--white);box-shadow:0 6px 24px rgba(61,52,68,.18)}
.btn{display:inline-block;background:var(--yellow);color:var(--white);font-size:13px;font-weight:700;border-radius:22px;padding:11px 26px;letter-spacing:.5px;line-height:18px}

/* about */
.about{left:0;top:1072px;width:1200px;height:628px;background:linear-gradient(180deg,#f6f7f4 0%,#f2f5ef 100%)}
.about h2{position:absolute;top:80px;width:100%;text-align:center}
.about-text{position:absolute;left:150px;top:150px;width:900px;text-align:center;font-size:15px;line-height:24px;color:var(--ink-soft)}
.about-text p+p{margin-top:14px}
.about-text .btn{margin-top:22px}
.landscape{left:0;top:1340px;width:1200px;height:360px;
  background:
    radial-gradient(ellipse 260px 110px at 980px 260px,#6f7d55 0%,rgba(111,125,85,0) 70%),
    radial-gradient(ellipse 320px 120px at 180px 270px,#5f7048 0%,rgba(95,112,72,0) 70%),
    linear-gradient(180deg,rgba(242,245,239,0) 0%,#e3e8df 20%,#c9d4c0 42%,#97a882 62%,#6c7f55 80%,#f4f4f4 100%)}

/* gallery */
.gallery{left:0;top:1700px;width:1200px;height:1088px;background:#f4f4f4}
.skyline{left:640px;top:1840px;width:560px;height:948px;
  background:
    radial-gradient(ellipse 120px 300px at 240px 420px,#d4d7d6 0%,#b9bdbb 40%,rgba(185,189,187,0) 75%),
    linear-gradient(180deg,#dfe8ee 0%,#cad8e0 40%,#e7d9c3 58%,#9fb08a 74%,#6f8a5a 88%,#f4f4f4 100%);
  -webkit-mask-image:linear-gradient(90deg,transparent 0%,#000 30%);mask-image:linear-gradient(90deg,transparent 0%,#000 30%)}
.project{width:306px;height:276px;background:var(--white);box-shadow:0 3px 12px rgba(61,52,68,.15);padding:12px}
.project .photo{height:198px;border-radius:16px}
.project h3{margin-top:22px;text-align:center;font-size:17px;font-weight:700;color:var(--ink)}

/* customers */
.customers{left:0;top:2788px;width:1200px;height:344px;background:var(--purple)}
.customers h2{position:absolute;top:96px;width:100%;text-align:center;color:var(--white)}
.client{top:164px;width:184px;height:76px;background:var(--white);display:flex;align-items:center;justify-content:center;gap:8px;font-family:"Quicksand",sans-serif;font-weight:700;font-size:20px;color:var(--purple)}
.client i{width:18px;height:18px;border-radius:50%;background:var(--purple-mid)}
.chev{top:186px;color:var(--white);font-size:30px;line-height:30px;font-family:"Quicksand",sans-serif}

/* calculators */
.calculators{left:0;top:3132px;width:1200px;height:708px;background:var(--white)}
.calculators h2{position:absolute;top:110px;width:100%;text-align:center}
.city{left:0;top:420px;width:1200px;height:288px;
  background:
    radial-gradient(ellipse 700px 120px at 600px 300px,#b8bcc3 0%,rgba(184,188,195,0) 70%),
    radial-gradient(ellipse 300px 60px at 600px 150px,#c9ccd2 0%,rgba(201,204,210,0) 70%),
    linear-gradient(180deg,#fff 0%,#eceef0 30%,#d6d9de 60%,#c4c8ce 100%)}
.calc{top:200px;width:300px;text-align:center}
.calc svg{display:block;margin:0 auto 18px}
.calc h3{font-size:17px;font-weight:700;line-height:22px;color:var(--ink)}
.calc p{margin-top:12px;font-size:13px;line-height:19px;color:var(--ink-soft)}

/* contact */
.contact{left:0;top:3800px;width:1200px;height:540px}
.contact h2{position:absolute;top:116px;width:100%;text-align:center}
.field{height:72px;background:var(--white);display:flex;align-items:center;gap:10px;padding:0 18px;font-size:14px;color:var(--ink-soft)}
.field.message{align-items:flex-start;padding-top:22px}
.submit{left:532px;top:420px;width:136px;height:50px;background:var(--purple-deep);color:var(--white);font-size:13px;font-weight:700;display:flex;align-items:center;justify-content:center;letter-spacing:.5px}
.chat{left:1112px;top:4316px;width:52px;height:52px;border-radius:50%;background:var(--white);box-shadow:0 2px 10px rgba(61,52,68,.25);z-index:3}

/* footer */
.site-footer{left:0;top:4340px;width:1200px;height:432px;background:linear-gradient(180deg,var(--purple) 0%,var(--purple) 70%,#5d3889 100%)}
.badge{top:60px;width:124px;height:80px;background:var(--white);border-radius:4px;display:flex;align-items:center;justify-content:center}
.badge span{width:40px;height:40px;border-radius:50%;background:var(--yellow-soft)}
.footer-nav{top:172px;width:100%;display:flex;justify-content:center;gap:18px;font-size:14px;color:var(--white);text-transform:uppercase}
.info{top:212px;width:320px;text-align:center;color:var(--white)}
.info .icon{width:48px;height:48px;border-radius:50%;background:var(--yellow);margin:0 auto 12px;display:flex;align-items:center;justify-content:center}
.info h4{font-size:17px;font-weight:700;margin-bottom:6px}
.info p{font-size:14px;line-height:20px}
.copyright{left:0;top:4772px;width:1200px;height:96px;background:var(--purple-deep);color:var(--white);font-size:14px;display:flex;align-items:center;justify-content:center}
</style>
</head>
<body>

<header class="site-header abs">
  <div class="brand abs"><span class="brand-dot"></span>Floravine</div>
  <div class="call-pill abs">
    <svg width="18" height="18" viewBox="0 0 24 24"><path d="M6.6 10.8a15 15 0 0 0 6.6 6.6l2.2-2.2c.3-.3.7-.4 1-.2 1.1.4 2.3.6 3.6.6.6 0 1 .4 1 1V20c0 .6-.4 1-1 1A17 17 0 0 1 3 4c0-.6.4-1 1-1h3.5c.6 0 1 .4 1 1 0 1.3.2 2.5.6 3.6.1.3 0 .7-.2 1z" fill="#fff"/></svg>
    Call Us Anytime : +1 555 240 7781
  </div>
  <nav class="main-nav abs">
    <a class="active">Home</a><a>Services</a><a>Gallery</a><a>Calculator</a><a>Testimonials</a><a>Portfolio</a><a>Contact</a><a>Blog</a>
  </nav>
</header>

<section class="hero abs" role="img" aria-label="Video still of a modern house with a green lawn under a clear sky">
  <div class="hero-copy abs">Bring goods straight from factory and cut away the middleman costing so client can have a better quality with affordable price</div>
  <div class="play-btn abs"><svg width="56" height="56" viewBox="0 0 56 56"><path d="M23 18l16 10-16 10z" fill="#fff"/></svg></div>
  <div class="hero-arrow abs" style="left:24px"><svg width="44" height="44" viewBox="0 0 44 44"><path d="M25 14l-8 8 8 8" stroke="#3D3444" stroke-width="3" fill="none"/></svg></div>
  <div class="hero-arrow abs" style="left:1132px"><svg width="44" height="44" viewBox="0 0 44 44"><path d="M19 14l8 8-8 8" stroke="#3D3444" stroke-width="3" fill="none"/></svg></div>
</section>

<section class="services abs">
  <div class="service abs" style="left:0;top:30px"><div class="photo" style="background:radial-gradient(circle at 50% 30%,#f4f4f6 0%,#d9d7dc 45%,#8c8794 100%)" role="img" aria-label="Photo of a furnished office interior"></div>Office Interior<br>Design</div>
  <div class="service abs" style="left:240px;top:30px"><div class="photo" style="background:radial-gradient(circle at 45% 35%,#f3e6e2 0%,#c9524a 45%,#3d3444 100%)" role="img" aria-label="Photo of a renovated office with red accents"></div>Office Renovation</div>
  <div class="service-card abs"></div>
  <div class="service abs" style="left:480px;top:0"><div class="photo" style="background:linear-gradient(160deg,#ffffff 0%,#eef0f3 50%,#c9cdd4 100%)" role="img" aria-label="Photo of a floor plan on a desk"></div>Office Space Planning<br><span class="btn" style="margin-top:18px">READ MORE ›</span></div>
  <div class="service abs" style="left:720px;top:30px"><div class="photo" style="background:radial-gradient(circle at 60% 35%,#f6efe6 0%,#d8c4ad 50%,#7d6a5a 100%)" role="img" aria-label="Photo of a designer working at a desk"></div>Office Partitioning</div>
  <div class="service abs" style="left:960px;top:30px"><div class="photo" style="background:radial-gradient(circle at 50% 40%,#b8e08c 0%,#5f9a3c 50%,#2f5a25 100%)" role="img" aria-label="Photo of an office with a green plant wall"></div>Office Reinstatement<br>Service</div>
</section>

<section class="about abs">
  <h2 class="section-title">ABOUT US</h2>
  <div class="about-text">
    <p>Floravine is an interior design and renovation company that specialises in office interior design and commercial fitout renovation. We always aim to provide premium quality services with competitive cost and ensuring our clients are pleased with the outcome.</p>
    <p>Since 2010 when the firm began, Floravine has amassed a wealth of experience in commercial interior design. Our team of dedicated and professional designers is committed to creating commercial spaces that stir clients' emotions. We are well versed in design work on retail stores, office buildings, F&amp;Bs as well as educational sites.</p>
    <span class="btn">READ MORE ›</span>
  </div>
</section>
<div class="landscape abs" role="img" aria-label="Photo of a misty green mountain landscape"></div>

<section class="gallery abs">
  <h2 class="section-title abs" style="left:112px;top:50px">PROJECT GALLERY</h2>
</section>
<div class="skyline abs" role="img" aria-label="Photo of a waterfront city landmark fountain at sunset"></div>
<article class="project abs" style="left:112px;top:1832px"><div class="photo" style="background:radial-gradient(ellipse at 50% 75%,#f08a2c 0%,#c66a24 25%,rgba(198,106,36,0) 45%),linear-gradient(180deg,#3d3444 0%,#6a5e56 45%,#d9cbb8 100%)" role="img" aria-label="Photo of a reception area with an orange counter"></div><h3>Harbourline Singapore</h3></article>
<article class="project abs" style="left:442px;top:1832px"><div class="photo" style="background:radial-gradient(circle at 30% 40%,#f7dc72 0%,#e3b834 45%,#9d7418 100%)" role="img" aria-label="Photo of a gold textured meeting room"></div><h3>TMCA Office</h3></article>
<article class="project abs" style="left:112px;top:2128px"><div class="photo" style="background:linear-gradient(180deg,#f7f3ec 0%,#e6dccd 45%,#c4ad8d 75%,#8f7858 100%)" role="img" aria-label="Photo of a bright open office with wood floor"></div><h3>Wayfarer Hotels</h3></article>
<article class="project abs" style="left:442px;top:2128px"><div class="photo" style="background:linear-gradient(180deg,#ece6dc 0%,#cdbfa8 40%,#94805f 75%,#5d4d3a 100%)" role="img" aria-label="Photo of an office corridor with wood finishes"></div><h3>Harbourline Kuala Lumpur</h3></article>
<article class="project abs" style="left:112px;top:2424px"><div class="photo" style="background:linear-gradient(90deg,#4a3c30 0%,#4a3c30 22%,#e9c66a 23%,#caa04a 60%,#8f6c28 100%)" role="img" aria-label="Photo of a reception with a gold feature wall"></div><h3>Sunridge Holdings</h3></article>
<article class="project abs" style="left:442px;top:2424px"><div class="photo" style="background:linear-gradient(180deg,#fafbfc 0%,#e4e7ea 50%,#aeb4ba 80%,#7d848b 100%)" role="img" aria-label="Photo of a white reception lobby"></div><h3>Vertex Singapore</h3></article>

<section class="customers abs">
  <h2 class="section-title">CUSTOMERS</h2>
  <span class="chev abs" style="left:44px">‹</span>
  <div class="client abs" style="left:112px"><i></i>Lumen</div>
  <div class="client abs" style="left:312px"><i></i>Mosaic</div>
  <div class="client abs" style="left:512px"><i></i>Kestrel</div>
  <div class="client abs" style="left:712px"><i></i>Aster</div>
  <div class="client abs" style="left:912px"><i></i>Oakline</div>
  <span class="chev abs" style="left:1140px">›</span>
</section>

<section class="calculators abs">
  <div class="city abs" role="img" aria-label="Photo of a curved architectural walkway facing a city skyline"></div>
  <h2 class="section-title">OUR CALCULATORS</h2>
  <div class="calc abs" style="left:130px">
    <svg width="72" height="72" viewBox="0 0 72 72"><rect x="10" y="26" width="18" height="40" fill="#F8CF3A"/><rect x="32" y="8" width="22" height="58" fill="#6B429C"/><rect x="56" y="34" width="10" height="32" fill="#FFC000"/><path d="M37 16h4M45 16h4M37 26h4M45 26h4M37 36h4M45 36h4M37 46h4M45 46h4" stroke="#fff" stroke-width="3"/></svg>
    <h3>Office Floor Space<br>Calculator</h3>
    <p>Unsure how much office space do you need for renovation? Use our office space calculator here.</p>
  </div>
  <div class="calc abs" style="left:450px">
    <svg width="72" height="72" viewBox="0 0 72 72"><circle cx="36" cy="30" r="24" fill="#FFC000"/><circle cx="36" cy="30" r="16" fill="#6B429C"/><text x="36" y="37" text-anchor="middle" font-family="Open Sans,sans-serif" font-weight="700" font-size="20" fill="#fff">$</text><rect x="14" y="58" width="44" height="8" rx="3" fill="#F8CF3A"/></svg>
    <h3>Renovation Budget<br>Calculator</h3>
    <p>How much should you budget for office renovation? Try out our renovation budget calculator here.</p>
  </div>
  <div class="calc abs" style="left:770px">
    <svg width="72" height="72" viewBox="0 0 72 72"><rect x="12" y="6" width="38" height="52" rx="3" fill="#6B429C"/><path d="M20 18h22M20 28h22M20 38h14" stroke="#fff" stroke-width="3"/><circle cx="50" cy="52" r="16" fill="#FFC000"/><path d="M50 44v9h7" stroke="#fff" stroke-width="3" fill="none"/></svg>
    <h3>Project Timeline<br>Calculator</h3>
    <p>In order to know your office renovation and relocation timeframe, use the project timeline calculator.</p>
  </div>
</section>

<section class="contact abs">
  <svg class="abs" style="left:0;top:0" width="1200" height="540" viewBox="0 0 1200 540"><path d="M0 70 C 300 10, 700 0, 1000 40 C 1100 52, 1160 30, 1200 0 V540 H0 Z" fill="#FFC000"/></svg>
  <h2 class="section-title">GET IN TOUCH</h2>
  <div class="field abs" style="left:112px;top:180px;width:312px"><svg width="14" height="14" viewBox="0 0 14 14"><circle cx="7" cy="4" r="3" fill="#6F6676"/><path d="M1 14c0-4 3-6 6-6s6 2 6 6z" fill="#6F6676"/></svg>Name</div>
  <div class="field abs" style="left:444px;top:180px;width:312px"><svg width="14" height="12" viewBox="0 0 14 12"><rect width="14" height="12" fill="#6F6676"/><path d="M0 0l7 6 7-6" stroke="#fff" fill="none"/></svg>Email address</div>
  <div class="field abs" style="left:776px;top:180px;width:312px"><svg width="14" height="14" viewBox="0 0 24 24"><path d="M6.6 10.8a15 15 0 0 0 6.6 6.6l2.2-2.2c.3-.3.7-.4 1-.2 1.1.4 2.3.6 3.6.6.6 0 1 .4 1 1V20c0 .6-.4 1-1 1A17 17 0 0 1 3 4c0-.6.4-1 1-1h3.5c.6 0 1 .4 1 1 0 1.3.2 2.5.6 3.6.1.3 0 .7-.2 1z" fill="#6F6676"/></svg>Phone</div>
  <div class="field message abs" style="left:112px;top:272px;width:976px;height:136px"><svg width="14" height="14" viewBox="0 0 14 14"><path d="M1 13l1-4 8-8 3 3-8 8z" fill="#6F6676"/></svg>Message</div>
  <div class="submit abs">SUBMIT NOW</div>
</section>
<div class="chat abs"><svg width="52" height="52" viewBox="0 0 52 52"><path d="M16 18h20v13H24l-6 5v-5h-2z" fill="#3D3444"/></svg></div>

<footer class="site-footer abs">
  <div class="badge abs" style="left:260px"><span></span></div>
  <div class="badge abs" style="left:448px"><span></span></div>
  <div class="badge abs" style="left:632px"><span></span></div>
  <div class="badge abs" style="left:820px"><span></span></div>
  <nav class="footer-nav abs"><span>Home</span>/<span>Services</span>/<span>Gallery</span>/<span>Calculator</span>/<span>Testimonials</span>/<span>Blog</span>/<span>Contact Us</span></nav>
  <div class="info abs" style="left:68px">
    <div class="icon"><svg width="20" height="24" viewBox="0 0 20 24"><path d="M10 0a9 9 0 0 1 9 9c0 7-9 15-9 15S1 16 1 9a9 9 0 0 1 9-9z" fill="#fff"/><circle cx="10" cy="9" r="3.5" fill="#FFC000"/></svg></div>
    <h4>Address :</h4>
    <p>8 Fernleaf Road<br>#04-11 Canopy House<br>Singapore 168402</p>
  </div>
  <div class="info abs" style="left:440px">
    <div class="icon"><svg width="20" height="20" viewBox="0 0 24 24"><path d="M6.6 10.8a15 15 0 0 0 6.6 6.6l2.2-2.2c.3-.3.7-.4 1-.2 1.1.4 2.3.6 3.6.6.6 0 1 .4 1 1V20c0 .6-.4 1-1 1A17 17 0 0 1 3 4c0-.6.4-1 1-1h3.5c.6 0 1 .4 1 1 0 1.3.2 2.5.6 3.6.1.3 0 .7-.2 1z" fill="#fff"/></svg></div>
    <h4>Phone :</h4>
    <p>+65 6210 3387</p>
  </div>
  <div class="info abs" style="left:812px">
    <div class="icon"><svg width="22" height="16" viewBox="0 0 22 16"><rect width="22" height="16" rx="2" fill="#fff"/><path d="M1 1l10 8 10-8" stroke="#FFC000" stroke-width="2" fill="none"/></svg></div>
    <h4>Email address :</h4>
    <p>hello@floravine.sg</p>
  </div>
</footer>
<div class="copyright abs">© Copyrights 2023 Floravine Pte Ltd | All Rights Reserved</div>

</body>
</html>
```